Request for Business Card Design

Hi. My name is Marlene, I am looking for a new business card design for my company, Quarrow Signal Instruments, LLC. I really like the design you did for Tarsel Venture and was hoping you could do something similar using our full logo and our mark. I am also open to any raised texture design using our mark. I have attached our full logo, which would need to be somewhere on the card, as well as the mark in both outline and full form, as well as our brand colors / guide. The card does not have to be white, as long as our logo and mark appear. I actually like darker colored business cards more, but am open to all options. If you are interested in working with me, please let me know. We would also take the business card design into letterhead design if you can do that.

```html
<!DOCTYPE html>
<html lang="en">
<head>
<meta charset="utf-8">
<title>Quarrow Signal Instruments – Business Card</title>
<link rel="stylesheet" href="https://fonts.googleapis.com/css2?family=Open+Sans:wght@400;600;700&display=swap">
<style>
  :root {
    --stage: #3b3b3d;
    --card-black: #151516;
    --card-front-light: #2a2a2b;
    --card-front-dark: #0c0c0d;
    --brand-blue: #1596c6;
    --ink-white: #f4f4f4;
  }
  * { box-sizing: border-box; margin: 0; padding: 0; }
  html, body {
    width: 1200px;
    height: 689px;
    overflow: hidden;
    background: var(--stage);
    font-family: "Open Sans", sans-serif;
  }
  .canvas {
    position: relative;
    width: 1200px;
    height: 689px;
  }
  .card {
    position: absolute;
    top: 196px;
    width: 520px;
    height: 297px;
    border-radius: 14px;
    overflow: hidden;
    background: var(--card-black);
  }
  .card--front { left: 50px; }
  .card--back { left: 630px; }

  .front-texture {
    position: absolute;
    inset: 0;
    background: linear-gradient(120deg, var(--card-front-light) 0%, #1b1b1c 45%, var(--card-front-dark) 100%);
  }

  .lockup {
    position: absolute;
    display: flex;
    align-items: center;
    gap: 12px;
  }
  .lockup__dot {
    width: 26px;
    height: 26px;
    border-radius: 50%;
    background: var(--brand-blue);
    flex: none;
  }
  .lockup__name {
    color: var(--ink-white);
    font-weight: 700;
    font-size: 21px;
    line-height: 1.05;
    letter-spacing: 0.06em;
    text-transform: uppercase;
  }
  .card--front .lockup { left: 120px; top: 124px; }
  .card--back .lockup { left: 34px; top: 152px; }
  .card--back .lockup__name { font-size: 17px; }

  .divider {
    position: absolute;
    left: 300px;
    top: 40px;
    width: 1.5px;
    height: 217px;
    background: var(--brand-blue);
  }
  .contact {
    position: absolute;
    left: 318px;
    top: 44px;
    color: var(--ink-white);
    font-size: 12px;
    line-height: 1.45;
  }
  .contact__name {
    color: var(--brand-blue);
    font-weight: 700;
    font-size: 17px;
    letter-spacing: 0.02em;
    text-transform: uppercase;
    line-height: 1.1;
  }
  .contact__role { font-size: 12.5px; margin-bottom: 18px; }
  .contact__list { list-style: none; margin-bottom: 18px; }
  .contact__list li { display: flex; align-items: center; gap: 7px; }
  .contact__list svg { width: 10px; height: 10px; fill: var(--brand-blue); flex: none; }
</style>
</head>
<body>
<main class="canvas">
  <section class="card card--front" aria-label="Card front">
    <div class="front-texture" role="img" aria-label="Raised tone-on-tone texture of the company mark repeated across the card"></div>
    <div class="lockup">
      <span class="lockup__dot"></span>
      <span class="lockup__name">Quarrow<br>Signal Instruments</span>
    </div>
  </section>

  <section class="card card--back" aria-label="Card back">
    <div class="lockup">
      <span class="lockup__dot"></span>
      <span class="lockup__name">Quarrow<br>Signal Instruments</span>
    </div>
    <div class="divider"></div>
    <div class="contact">
      <p class="contact__name">Dana Whitlow</p>
      <p class="contact__role">Managing Director</p>
      <ul class="contact__list">
        <li>
          <svg viewBox="0 0 10 10" aria-hidden="true"><path d="M2 0.5 L3.8 2.6 L2.8 3.8 Q4 6.2 6.2 7.2 L7.4 6.2 L9.5 8 L8.3 9.5 Q1 8.5 0.5 1.7 Z"/></svg>
          123 456 789
        </li>
        <li>
          <svg viewBox="0 0 10 10" aria-hidden="true"><path d="M0.5 2 H9.5 V8.5 H0.5 Z M0.5 2 L5 5.5 L9.5 2" stroke="#151516" stroke-width="0.8"/></svg>
          info@yourgmail.com
        </li>
        <li>
          <svg viewBox="0 0 10 10" aria-hidden="true"><circle cx="5" cy="5" r="4.5"/></svg>
          www.yourwebsite.com
        </li>
      </ul>
      <p class="contact__address">Your address, City<br>State, Zip 1234</p>
    </div>
  </section>
</main>
</body>
</html>
```